Business Card Design - Property Management & Real Estate Services

I need a business card design for my company that I can print ZEPLA Cards. The company is called Brindle Management Company. It is a property management and real estate company. The design has to be clean and modern. I need two versions. One for my employee and one for me. However, the design will be the same, just different text. You can get a feel for the company by looking at our website at www.brindlemanagement.example.

Industry/Entity Type

Property Management

Contact Information for Business Card

I will be using ZEPLA.com to print my cards. I will most likely use the rounded edges card. I need two versions, however, they will be the same design. I need one for me and my employee.

Colors
3276b5
33a6d7

Requirements
Must have
• Company Logo
• Name of person
• Property Management & Real Estate Service
• Phone
• Email
• Website
• Address
• A space to place a QR code

```html
<!DOCTYPE html>
<html lang="en">
<head>
<meta charset="UTF-8">
<title>Brindle Management – Business Cards</title>
<link href="https://fonts.googleapis.com/css2?family=Montserrat:wght@500&family=Roboto:wght@400&family=Roboto+Condensed:ital,wght@1,700&display=swap" rel="stylesheet">
<style>
  :root {
    --page-bg: #2b2b2d;
    --card-black: #1c1d20;
    --silver: #c9cbd0;
    --brand-blue: #3276b5;
    --brand-sky: #33a6d7;
    --wave-light: #6ea3dc;
    --band-blue: #1f5fb8;
    --text-white: #ffffff;
    --text-muted: #5a5e66;
  }
  * { margin: 0; padding: 0; box-sizing: border-box; }
  html, body { width: 799px; height: 1200px; overflow: hidden; }
  body {
    background: var(--page-bg);
    font-family: "Roboto", sans-serif;
    position: relative;
  }
  .card {
    position: absolute;
    left: 90px;
    width: 620px;
    height: 360px;
    border-radius: 26px;
    background: var(--card-black);
    overflow: hidden;
  }
  .card--front { top: 140px; }
  .card--back { top: 720px; }

  .wordmark {
    font-family: "Montserrat", sans-serif;
    font-weight: 500;
    text-transform: uppercase;
    line-height: 1;
  }
  .card--front .wordmark {
    position: absolute;
    left: 0; right: 0; top: 146px;
    text-align: center;
    color: var(--silver);
    font-size: 40px;
    letter-spacing: 6px;
  }
  .card--front .wordmark small {
    display: block;
    font-size: 15px;
    letter-spacing: 11px;
    margin-top: 10px;
  }
  .tagline {
    font-family: "Roboto", sans-serif;
    font-weight: 400;
    text-transform: none;
  }
  .card--front .tagline {
    position: absolute;
    left: 0; right: 0; top: 226px;
    text-align: center;
    color: var(--silver);
    font-size: 13px;
    letter-spacing: 1px;
  }

  .card--back .wordmark {
    position: absolute;
    left: 44px; top: 70px;
    color: var(--brand-blue);
    font-size: 34px;
    letter-spacing: 5px;
  }
  .card--back .wordmark small {
    display: block;
    font-size: 13px;
    letter-spacing: 9px;
    margin-top: 8px;
  }
  .card--back .tagline {
    position: absolute;
    left: 46px; top: 136px;
    color: var(--brand-sky);
    font-size: 11.5px;
    letter-spacing: .5px;
  }

  .wave { position: absolute; left: 0; top: 0; width: 620px; height: 360px; }

  .holder {
    position: absolute;
    right: 38px; top: 74px;
    text-align: right;
  }
  .holder__name {
    font-family: "Roboto Condensed", sans-serif;
    font-style: italic;
    font-weight: 700;
    font-size: 22px;
    color: var(--brand-blue);
  }
  .holder__role {
    font-size: 13px;
    color: var(--text-muted);
    margin-top: 2px;
  }

  .qr-space {
    position: absolute;
    left: 40px; top: 252px;
    width: 80px; height: 80px;
    border: 1.5px dashed rgba(255,255,255,.7);
    border-radius: 6px;
  }

  .contact {
    position: absolute;
    right: 34px; top: 244px;
    list-style: none;
    color: var(--text-white);
    font-size: 16px;
    text-align: right;
  }
  .contact li {
    display: flex;
    justify-content: flex-end;
    align-items: center;
    gap: 10px;
    line-height: 24px;
  }
  .contact svg { width: 15px; height: 15px; flex: none; }
  .contact .no-icon { padding-right: 25px; }
</style>
</head>
<body>

  <section class="card card--front" aria-label="Card front">
    <div class="wordmark">Brindle<small>Management</small></div>
    <p class="tagline">Property Management &amp; Real Estate Services</p>
  </section>

  <section class="card card--back" aria-label="Card back">
    <svg class="wave" viewBox="0 0 620 360" aria-hidden="true">
      <path d="M0,168 C160,196 330,226 620,170 L620,186 C330,246 160,214 0,190 Z" fill="var(--wave-light)"/>
      <path d="M0,204 C170,236 340,268 620,200 L620,360 L0,360 Z" fill="var(--band-blue)"/>
      <path d="M0,214 C180,246 360,272 620,214" fill="none" stroke="var(--brand-blue)" stroke-width="2" opacity=".5"/>
    </svg>

    <div class="wordmark">Brindle<small>Management</small></div>
    <p class="tagline">Property Management &amp; Real Estate Services</p>

    <div class="holder">
      <p class="holder__name">Mateo R. Salinas</p>
      <p class="holder__role">Founder</p>
    </div>

    <div class="qr-space" role="img" aria-label="Space reserved for QR code"></div>

    <ul class="contact">
      <li>(305) 555-0142
        <svg viewBox="0 0 16 16" aria-hidden="true"><path d="M4 1.5 6.3 4 5 5.6c.8 2 2.4 3.6 4.4 4.4L11 8.7l2.5 2.3-1.4 2.6C6.5 13.4 2.6 9.5 1.4 4.6Z" fill="#fff"/></svg>
      </li>
      <li>brindlemanagement.example
        <svg viewBox="0 0 16 16" aria-hidden="true"><circle cx="8" cy="8" r="6.3" fill="none" stroke="#fff" stroke-width="1.3"/><ellipse cx="8" cy="8" rx="2.8" ry="6.3" fill="none" stroke="#fff" stroke-width="1.1"/><path d="M1.7 8h12.6" stroke="#fff" stroke-width="1.1"/></svg>
      </li>
      <li>mateo@brindlemanagement.example
        <svg viewBox="0 0 16 16" aria-hidden="true"><rect x="1.5" y="3.5" width="13" height="9" fill="none" stroke="#fff" stroke-width="1.4"/><path d="M1.5 3.5 8 9l6.5-5.5" fill="none" stroke="#fff" stroke-width="1.4"/></svg>
      </li>
      <li class="no-icon">480 Harbor Ave #210 Miami, FL 33130</li>
    </ul>
  </section>

</body>
</html>
```